Document Processing Services and Solutions for School Systems

I am looking to design a brochure for both Digital and Paper use. I can supply the written content. Would be looking for an overall design of the brochure with provided content worked into it.

```html
<!DOCTYPE html>
<html lang="en">
<head>
<meta charset="utf-8">
<title>Keystone Docuworks – School Document Management Brochure</title>
<link rel="stylesheet" href="https://fonts.googleapis.com/css2?family=Archivo+Black&family=Exo+2:ital,wght@0,400;0,700;0,800;1,400&family=Michroma&display=swap">
<style>
  :root {
    --navy: #1b1c72;
    --gold: #d19c1d;
    --paper: #f4f4f4;
    --backdrop: #8a8a8a;
    --white: #ffffff;
    --photo-a: #8c96a8;
    --photo-b: #c7b497;
  }
  * { box-sizing: border-box; margin: 0; padding: 0; }
  html, body { width: 1200px; height: 1200px; overflow: hidden; background: var(--backdrop); }
  .spread {
    position: absolute; left: 50px; top: 244px;
    width: 1100px; height: 712px; display: flex;
    box-shadow: 0 18px 40px rgba(0,0,0,.25);
  }
  .panel { position: relative; width: 550px; height: 712px; overflow: hidden; }
  .back-cover { background: var(--navy); color: var(--white); }
  .front-cover { background: var(--paper); }
  .panel svg.frame { position: absolute; inset: 0; }

  .cta { position: absolute; left: 60px; top: 215px; width: 430px; text-align: center; }
  .cta-title { font-family: "Michroma", sans-serif; font-size: 19px; letter-spacing: .5px; margin-bottom: 14px; }
  .cta-title strong { font-family: "Exo 2", sans-serif; font-weight: 800; font-size: 22px; }
  .cta-text { font-family: "Exo 2", sans-serif; font-style: italic; font-size: 14px; line-height: 1.45; letter-spacing: .6px; margin-bottom: 22px; }
  .contact-list { list-style: none; text-align: left; display: inline-block; }
  .contact-list li { display: flex; align-items: center; gap: 12px; font-family: "Exo 2", sans-serif; font-size: 19px; letter-spacing: 1px; margin-bottom: 10px; }
  .contact-list li.phone { font-weight: 800; font-size: 23px; letter-spacing: 1.5px; }
  .contact-list svg { width: 22px; height: 22px; flex: none; }

  .brand { position: absolute; right: 28px; top: 100px; display: flex; align-items: center; gap: 8px; }
  .brand-mark { width: 12px; height: 12px; background: var(--gold); }
  .brand-name { font-family: "Exo 2", sans-serif; font-weight: 800; color: var(--navy); font-size: 21px; line-height: 1.05; text-align: right; }

  .headline { position: absolute; left: 28px; right: 28px; top: 525px; color: var(--navy); }
  .headline-lead { font-family: "Michroma", sans-serif; font-size: 31px; letter-spacing: 1px; }
  .headline-main { font-family: "Archivo Black", sans-serif; font-size: 78px; line-height: .95; letter-spacing: 1px; }
  .headline-sub { font-family: "Exo 2", sans-serif; font-weight: 800; font-size: 17px; letter-spacing: 1.5px; line-height: 1.2; margin-top: 6px; }
</style>
</head>
<body>
<main class="spread">
  <section class="panel back-cover">
    <svg class="frame" viewBox="0 0 550 712" width="550" height="712">
      <polyline points="0,668 22,668 38,652 70,652 84,670 550,670" fill="none" stroke="var(--gold)" stroke-width="6"/>
    </svg>
    <div class="cta">
      <h2 class="cta-title">GET STARTED <strong>TODAY!</strong></h2>
      <p class="cta-text">Let us help you modernize your document processing system. Contact us for a free consultation and discover how our solutions can transform your school's document management.</p>
      <ul class="contact-list">
        <li class="phone">
          <svg viewBox="0 0 24 24"><rect x="1" y="1" width="22" height="22" rx="4" fill="var(--white)"/><path d="M8 5c-2 1-2 4 0 8s5 6 7 5l1-2-3-2-1 1c-1-1-2-2-3-4l1-1-1-3z" fill="var(--navy)"/></svg>
          555-014-2290
        </li>
        <li>
          <svg viewBox="0 0 24 24"><rect x="1.5" y="5" width="21" height="14" fill="none" stroke="var(--white)" stroke-width="1.5"/><polyline points="1.5,5 12,13 22.5,5" fill="none" stroke="var(--white)" stroke-width="1.5"/></svg>
          hello@keystonedocs.com
        </li>
        <li>
          <svg viewBox="0 0 24 24"><circle cx="12" cy="12" r="10" fill="none" stroke="var(--white)" stroke-width="1.5"/><ellipse cx="12" cy="12" rx="4.5" ry="10" fill="none" stroke="var(--white)" stroke-width="1.5"/><line x1="2" y1="12" x2="22" y2="12" stroke="var(--white)" stroke-width="1.5"/></svg>
          www.keystonedocs.com
        </li>
      </ul>
    </div>
  </section>

  <section class="panel front-cover">
    <svg class="frame" viewBox="0 0 550 712" width="550" height="712">
      <defs>
        <linearGradient id="photoTone" x1="0" y1="0" x2="1" y2="1">
          <stop offset="0" stop-color="var(--photo-a)"/>
          <stop offset="1" stop-color="var(--photo-b)"/>
        </linearGradient>
      </defs>
      <polyline points="0,128 150,128 178,72 240,72 290,150 550,232" fill="none" stroke="var(--gold)" stroke-width="7"/>
      <polygon role="img" aria-label="Photo of a team working at computers in a bright open office"
               points="0,180 190,115 258,185 550,275 550,500 0,430" fill="url(#photoTone)"/>
      <polyline points="0,180 190,115 258,185 550,275" fill="none" stroke="var(--navy)" stroke-width="4"/>
      <line x1="0" y1="430" x2="550" y2="500" stroke="var(--navy)" stroke-width="4"/>
      <line x1="0" y1="444" x2="550" y2="514" stroke="var(--gold)" stroke-width="6"/>
    </svg>
    <div class="brand">
      <span class="brand-name">Keystone<br>Docuworks Inc</span>
      <span class="brand-mark"></span>
    </div>
    <div class="headline">
      <p class="headline-lead">TRANSFORM YOUR</p>
      <h1 class="headline-main">SCHOOL’S</h1>
      <p class="headline-sub">DOCUMENT MANAGEMENT WITH OUR<br>COMPREHENSIVE SOLUTIONS</p>
    </div>
  </section>
</main>
</body>
</html>
```